Tallwick Home Services Web Site

Design Web site with 3-4 pages: Home, About Us, Services and Order form / Schedule Appointment (which will likely be link to Method App and Quickbooks integration.)
Services include: Dryer Vent Cleaning, AC Cleaning, Difficult-to-Reach Light Bulb replacement, Wood Repair and Home Maintenance Plans including Fire Safety Checks and Filter Replacement.

Target Market(s)

Luxury Home Owners, Professionals (Dr's/lawyers) and Seniors

Industry/Entity Type

Home Maintenance

Coding

Coded - Design and coding required

Requirements
Must have
• Tagline - Where Home Maintenance is Elementary

```html
<!DOCTYPE html>
<html lang="en">
<head>
<meta charset="utf-8">
<title>Tallwick Home Services</title>
<link href="https://fonts.googleapis.com/css2?family=Montserrat:wght@400;500;600;700&family=Mulish:wght@400;600;700&display=swap" rel="stylesheet">
<style>
:root{
  --gold:#e2a826;
  --gold-dark:#cf9514;
  --slate:#6d6d72;
  --ink:#4a4a50;
  --mist:#efefef;
  --line:#d2d2d2;
  --white:#ffffff;
}
*{margin:0;padding:0;box-sizing:border-box}
html,body{width:1200px;height:4662px;overflow:hidden;background:var(--white)}
body{font-family:"Mulish",sans-serif;color:var(--ink)}
.page{position:relative;width:1200px;height:4662px;overflow:hidden}
.abs{position:absolute}
.heading{font-family:"Montserrat",sans-serif;font-weight:600;color:var(--ink);letter-spacing:.5px}
.btn{position:absolute;display:flex;align-items:center;justify-content:center;font-family:"Montserrat",sans-serif;font-weight:600;color:var(--white);background:var(--gold);letter-spacing:.5px}
.photo{position:absolute}
.wordmark{font-family:"Montserrat",sans-serif;font-weight:700;color:var(--gold);letter-spacing:2px}

/* header */
.topbar-item{position:absolute;display:flex;align-items:center;gap:10px;font-family:"Montserrat",sans-serif;font-size:14px;color:var(--ink)}
.dot-icon{width:38px;height:38px;border-radius:50%;background:var(--gold);display:flex;align-items:center;justify-content:center}
.nav{position:absolute;left:119px;top:72px;width:986px;height:68px;background:var(--slate);border-radius:34px}
.nav a{position:absolute;top:0;line-height:68px;font-family:"Montserrat",sans-serif;font-size:13px;font-weight:600;color:var(--white);text-decoration:none}
.nav .active::after{content:"";position:absolute;left:0;right:0;bottom:10px;height:3px;background:var(--gold)}
.logo-disc{position:absolute;left:493px;top:0;width:220px;height:170px;background:var(--white);border-radius:0 0 110px 110px;display:flex;align-items:center;justify-content:center;box-shadow:0 2px 6px rgba(0,0,0,.08)}

/* services */
.card{position:absolute;width:292px;background:var(--white);border:2px solid var(--line);border-radius:6px;overflow:hidden;text-align:center}
.card .pic{height:195px}
.card .badge{position:absolute;left:110px;top:158px;width:72px;height:72px;border-radius:50%;background:var(--gold);border:3px solid rgba(255,255,255,.6)}
.card h3{margin-top:58px;font-family:"Montserrat",sans-serif;font-size:18px;font-weight:600;color:var(--ink)}
.card p{margin:8px auto 0;width:230px;font-size:12px;line-height:17px;color:var(--ink)}
.card .more{margin:20px auto 0;width:130px;height:36px;line-height:36px;background:var(--slate);color:var(--white);font-family:"Montserrat",sans-serif;font-size:10px;font-weight:700}
.card.dark{background:var(--slate);border-color:var(--slate)}
.card.dark h3,.card.dark p{color:var(--white)}
.card.dark .more{background:transparent;border:1px solid var(--white)}

/* why */
.reason h4{font-family:"Montserrat",sans-serif;font-size:17px;font-weight:600;color:#333}
.reason p{font-size:11px;line-height:15px;color:var(--ink);margin-top:4px}
.reason{position:absolute;width:300px}
.reason.r{text-align:right}

/* testimonials */
.quote{position:absolute;background:var(--white);text-align:center;overflow:hidden}
.stars{color:var(--gold);letter-spacing:3px}
.qmark{position:absolute;font-family:Georgia,serif;color:#c8c8c8;font-weight:700}

/* form */
.field{position:absolute;background:var(--white);display:flex;align-items:center;padding-left:22px;gap:10px;font-size:15px;color:#777}

/* footer */
.fnav{position:absolute;top:4384px;font-family:"Montserrat",sans-serif;font-size:14px;font-weight:600;color:var(--ink)}
.bullet{position:absolute;top:4392px;width:5px;height:5px;background:var(--ink);border-radius:50%}
</style>
</head>
<body>
<div class="page">

  <!-- HERO -->
  <section class="abs" style="left:0;top:0;width:1200px;height:810px;background:var(--mist)">
    <div class="photo" role="img" aria-label="Technician replacing an air filter in a ceiling vent" style="left:360px;top:150px;width:840px;height:640px;background:linear-gradient(90deg,rgba(239,239,239,1) 0%,rgba(220,220,222,1) 30%,#c9cdd6 60%,#7f8fc8 85%,#6d7fc0 100%)"></div>
    <div class="abs" style="left:0;top:295px;width:8px;height:205px;background:var(--gold)"></div>
    <div class="abs heading" style="left:130px;top:280px;font-size:18px;font-weight:500;color:var(--slate);display:flex;align-items:center;gap:10px">TALLWICK HOME SERVICES <span style="display:inline-block;width:48px;height:1px;background:var(--slate)"></span></div>
    <h1 class="abs heading" style="left:128px;top:316px;font-size:46px;line-height:48px;font-weight:700">WHERE HOME<br>MAINTENANCE IS<br><span style="color:var(--gold)">ELEMENTARY</span></h1>
    <div class="btn" style="left:127px;top:492px;width:311px;height:62px;font-size:16px">BOOK AN APPOINTMENT</div>
    <svg class="abs" style="left:0;top:640px" width="1200" height="170" viewBox="0 0 1200 170">
      <path d="M0,160 Q560,40 1200,150 L1200,170 L0,170 Z" fill="#fff"/>
      <path d="M330,75 Q760,20 1200,150" fill="none" stroke="#e2a826" stroke-width="6"/>
    </svg>
  </section>

  <!-- HEADER -->
  <div class="topbar-item" style="left:145px;top:17px">
    <span class="dot-icon"><svg width="18" height="18" viewBox="0 0 18 18"><rect x="2" y="3" width="14" height="13" rx="2" fill="none" stroke="#fff" stroke-width="2"/><path d="M5 8h8" stroke="#fff" stroke-width="2"/></svg></span>SCHEDULE APPOINTMENT
  </div>
  <div class="topbar-item" style="left:783px;top:13px">
    <span class="dot-icon"><svg width="18" height="18" viewBox="0 0 24 24"><path d="M6.6 10.8a15 15 0 0 0 6.6 6.6l2.2-2.2c.3-.3.7-.4 1-.2 1.1.4 2.3.6 3.6.6.6 0 1 .4 1 1V20c0 .6-.4 1-1 1A17 17 0 0 1 3 4c0-.6.4-1 1-1h3.5c.6 0 1 .4 1 1 0 1.3.2 2.5.6 3.6.1.3 0 .7-.2 1z" fill="#fff"/></svg></span>CALL US NOW (+123) 555 0142
  </div>
  <nav class="nav">
    <a class="active" style="left:45px">HOME</a>
    <a style="left:137px">ABOUT US</a>
    <a style="left:258px">SERVICES</a>
    <a style="left:630px">WHY US</a>
    <a style="left:735px">CONTACT</a>
    <span class="btn" style="left:840px;top:14px;width:132px;height:40px;border-radius:20px;font-size:13px">BOOK NOW</span>
  </nav>
  <div class="logo-disc"><span class="wordmark" style="font-size:28px">TALLWICK</span></div>

  <!-- ABOUT -->
  <section>
    <svg class="abs" style="left:85px;top:800px" width="520" height="520" viewBox="0 0 520 520">
      <circle cx="259" cy="259" r="252" fill="none" stroke="#e2a826" stroke-width="7"/>
    </svg>
    <div class="photo" role="img" aria-label="Technician in a blue cap cleaning an air conditioning unit" style="left:108px;top:822px;width:474px;height:474px;border-radius:50%;background:linear-gradient(150deg,#f4f4f4 0%,#dfe2e6 45%,#9aa3ad 80%,#6f7782 100%)"></div>
    <div class="photo" role="img" aria-label="Smiling customer giving a thumbs up" style="left:345px;top:1063px;width:245px;height:245px;border-radius:50%;border:6px solid #fff;background:linear-gradient(160deg,#eef0f2 0%,#c9b8a8 55%,#8a7f7b 100%)"></div>
    <svg class="abs" style="left:530px;top:1210px" width="190" height="110" viewBox="0 0 190 110"><path d="M5,100 Q80,110 100,70 Q115,30 185,15" fill="none" stroke="#b8b8b8" stroke-width="1.5" stroke-dasharray="2 4"/></svg>
    <h2 class="abs heading" style="left:637px;top:855px;font-size:38px;line-height:44px;font-weight:700">ABOUT TALLWICK<br>HOME SERVICES</h2>
    <p class="abs" style="left:647px;top:982px;width:475px;font-size:18.5px;line-height:29px;color:var(--ink)">Lorem ipsum dolor sit amet, consectetur adipiscing elit, sed do eiusmod tempor incididunt ut labore et dolore magna aliqua. Quis ipsum suspendisse ultrices gravida. Risus commodo viverra maecenas accumsan lacus vel facilisis.</p>
    <div class="btn" style="left:647px;top:1155px;width:190px;height:55px;font-size:15px">LEARN MORE ›</div>
  </section>

  <!-- SERVICES -->
  <section class="abs" style="left:0;top:1408px;width:1200px;height:1099px;background:var(--mist)">
    <div class="abs" style="left:528px;top:-36px;width:144px;height:72px;border-radius:72px 72px 0 0;background:var(--mist)"></div>
    <h2 class="abs heading" style="left:0;width:1200px;top:60px;text-align:center;font-size:36px;font-weight:700">OUR SERVICES</h2>
    <svg class="abs" style="left:535px;top:110px" width="140" height="12" viewBox="0 0 140 12"><path d="M4,9 Q70,0 136,6" fill="none" stroke="#e2a826" stroke-width="4" stroke-linecap="round"/></svg>
  </section>

  <div class="card" style="left:148px;top:1573px;height:393px">
    <div class="pic" role="img" aria-label="Dryer vent grille" style="background:linear-gradient(180deg,#f2f2f2,#3a3a3c 60%,#d8d8d8)"></div>
    <span class="badge"></span>
    <h3>Dryer Vent Cleaning</h3>
    <p>Lorem ipsum dolor sit amet, consectetur adipiscing elit</p>
    <div class="more">LEARN MORE</div>
  </div>
  <div class="card dark" style="left:462px;top:1573px;height:393px">
    <div class="pic" role="img" aria-label="Gloved hand cleaning an AC unit" style="background:linear-gradient(160deg,#8fb1d8,#e9edf1 60%,#c9ccd0)"></div>
    <span class="badge"></span>
    <h3>AC Cleaning</h3>
    <p>Lorem ipsum dolor sit amet, consectetur adipiscing elit</p>
    <div class="more">LEARN MORE</div>
  </div>
  <div class="card" style="left:775px;top:1573px;height:387px">
    <div class="pic" role="img" aria-label="Worker replacing a ceiling light bulb" style="background:linear-gradient(180deg,#cfd4da,#8e97a2 60%,#e4e6e9)"></div>
    <span class="badge"></span>
    <h3>Difficult-to-Reach Light<br>Bulb replacement</h3>
    <p>Lorem ipsum dolor sit amet con</p>
    <div class="more">LEARN MORE</div>
  </div>
  <div class="card" style="left:302px;top:2002px;height:384px">
    <div class="pic" role="img" aria-label="Wooden drawer being repaired with a drill" style="background:linear-gradient(160deg,#b77a48,#d9a36b 50%,#8d5a34)"></div>
    <span class="badge"></span>
    <h3>Wood Repair</h3>
    <p>Lorem ipsum dolor sit amet, consectetur adipiscing elit</p>
    <div class="more">LEARN MORE</div>
  </div>
  <div class="card" style="left:615px;top:2002px;height:384px">
    <div class="pic" role="img" aria-label="Smoke detector on a ceiling" style="background:linear-gradient(170deg,#e9e6e3,#cdc7c2 50%,#d47a3e)"></div>
    <span class="badge"></span>
    <h3>Home Maintenance Plans</h3>
    <p>Fire Safety Checks<br>Filter Replacement</p>
    <div class="more">LEARN MORE</div>
  </div>

  <!-- WHY CHOOSE -->
  <section class="abs" style="left:0;top:2507px;width:1200px;height:603px;overflow:hidden">
    <h2 class="abs heading" style="left:0;width:1200px;top:48px;text-align:center;font-size:33px;font-weight:700">WHY CHOOSE TALLWICK</h2>
    <svg class="abs" style="left:527px;top:98px" width="146" height="12" viewBox="0 0 146 12"><path d="M4,9 Q73,0 142,6" fill="none" stroke="#e2a826" stroke-width="4" stroke-linecap="round"/></svg>
    <svg class="abs" style="left:0;top:0" width="1200" height="603" viewBox="0 0 1200 603">
      <circle cx="597" cy="603" r="320" fill="none" stroke="#d6d6d6" stroke-width="2"/>
      <circle cx="597" cy="603" r="285" fill="#e2a826"/>
      <g fill="#6d6d72" stroke="#fff" stroke-width="3">
        <circle cx="597" cy="268" r="24"/><circle cx="424" cy="319" r="24"/><circle cx="311" cy="447" r="24"/>
        <circle cx="784" cy="327" r="24"/><circle cx="889" cy="447" r="24"/>
      </g>
      <g fill="none" stroke="#fff" stroke-width="2">
        <path d="M587 268 l6 6 l12 -12"/><rect x="414" y="309" width="20" height="19" rx="2"/><path d="M302 447 l6 6 l12 -12"/>
        <circle cx="784" cy="327" r="10"/><path d="M784 320 v7 h6"/><path d="M879 452 l10 -12 l10 12 z"/>
      </g>
    </svg>
    <div class="reason" style="left:447px;top:176px;text-align:center"><h4>Expertise You Can Trust</h4><p>Lorem ipsum dolor sit amet,<br>consectetur adipiscing</p></div>
    <div class="reason r" style="left:76px;top:285px"><h4>Hassle-Free Scheduling</h4><p>Lorem ipsum dolor sit amet,<br>consectetur adipiscing</p></div>
    <div class="reason r" style="left:-32px;top:422px"><h4>Trust-focused</h4><p>Lorem ipsum dolor sit amet,<br>consectetur adipiscing</p></div>
    <div class="reason" style="left:834px;top:303px"><h4>Reliable &amp; On-Time</h4><p>Lorem ipsum dolor sit amet,<br>consectetur adipiscing</p></div>
    <div class="reason" style="left:936px;top:422px"><h4>Comprehensive Home Care</h4><p>Lorem ipsum dolor sit amet,<br>consectetur adipiscing</p></div>
  </section>

  <!-- TESTIMONIALS -->
  <section class="abs" style="left:0;top:3110px;width:1200px;height:590px;background:var(--slate)">
    <h2 class="abs heading" style="left:0;width:1200px;top:112px;text-align:center;font-size:36px;font-weight:700;color:var(--white)">WHAT PEOPLE SAYS</h2>
    <div class="quote" style="left:177px;top:230px;width:220px;height:208px;padding:30px 30px 0 30px">
      <div class="stars" style="font-size:18px;text-align:right">★★</div>
      <p style="font-size:12px;line-height:20px;text-align:right">"Lorem ipsum dolor sit amet, elit, sed do eiusmod tempor dolore magna aliqua. Quis trices gravida. Risus commodo cumsan lacus"</p>
      <p style="font-size:12px;font-weight:700;text-align:right;margin-top:6px">Dana</p>
    </div>
    <div class="quote" style="left:850px;top:230px;width:218px;height:208px;padding:30px 18px 0 20px;text-align:left">
      <div class="stars" style="font-size:18px">★★</div>
      <p style="font-size:12px;line-height:20px">, consectetur adipiscing r incididunt ut labore et ipsum suspendisse ul- do viverra maecenas ac- vel facilisis"</p>
      <p style="font-size:12px;font-weight:700;margin-top:10px">eyes</p>
      <span class="qmark" style="right:20px;bottom:-18px;font-size:70px">”</span>
    </div>
    <div class="quote" style="left:378px;top:208px;width:489px;height:262px;padding:36px 44px 0;box-shadow:0 4px 14px rgba(0,0,0,.15);z-index:2">
      <div class="stars" style="font-size:22px">★★★★★</div>
      <p style="font-size:15.5px;line-height:23px;margin-top:6px">"Lorem ipsum dolor sit amet, consectetur adipiscing elit, sed do eiusmod tempor incididunt ut labore et dolore magna aliqua. Quis ipsum suspendisse ultrices gravida. Risus commodo viverra maecenas accumsan lacus vel facilisis"</p>
      <p style="font-size:15px;font-weight:700;margin-top:14px">Dana Reyes</p>
      <span class="qmark" style="right:30px;bottom:-26px;font-size:90px">”</span>
    </div>
    <svg class="abs" style="left:573px;top:500px" width="100" height="44" viewBox="0 0 100 44">
      <circle cx="22" cy="22" r="21" fill="#e2a826"/><circle cx="74" cy="22" r="21" fill="#e2a826"/>
      <path d="M30 22H14M20 16l-6 6 6 6M66 22h16M76 16l6 6-6 6" fill="none" stroke="#fff" stroke-width="2.5" stroke-linecap="round" stroke-linejoin="round"/>
    </svg>
  </section>

  <!-- BOOK APPOINTMENT -->
  <section class="abs" style="left:123px;top:3759px;width:979px;height:536px;border-radius:14px;background:linear-gradient(120deg,#e6ab28 0%,#e9b43a 55%,#ddb04a 100%)" role="img" aria-label="Warm yellow toned photo of a person writing a booking">
  </section>
  <h2 class="abs heading" style="left:123px;width:979px;top:3833px;text-align:center;font-size:36px;font-weight:700;color:var(--white)">BOOK AN APPOINTMENT</h2>
  <div class="field" style="left:244px;top:3924px;width:362px;height:53px">
    <svg width="14" height="14" viewBox="0 0 14 14"><circle cx="7" cy="4" r="3.2" fill="#bbb"/><path d="M1 14c0-4 3-6 6-6s6 2 6 6z" fill="#bbb"/></svg>First name</div>
  <div class="field" style="left:621px;top:3924px;width:362px;height:53px">
    <svg width="14" height="14" viewBox="0 0 14 14"><circle cx="7" cy="4" r="3.2" fill="#bbb"/><path d="M1 14c0-4 3-6 6-6s6 2 6 6z" fill="#bbb"/></svg>Last name</div>
  <div class="field" style="left:244px;top:3989px;width:362px;height:53px">
    <svg width="15" height="15" viewBox="0 0 24 24"><path d="M6.6 10.8a15 15 0 0 0 6.6 6.6l2.2-2.2c.3-.3.7-.4 1-.2 1.1.4 2.3.6 3.6.6.6 0 1 .4 1 1V20c0 .6-.4 1-1 1A17 17 0 0 1 3 4c0-.6.4-1 1-1h3.5c.6 0 1 .4 1 1 0 1.3.2 2.5.6 3.6.1.3 0 .7-.2 1z" fill="#bbb"/></svg>Email address</div>
  <div class="field" style="left:621px;top:3989px;width:362px;height:53px">
    <svg width="15" height="12" viewBox="0 0 15 12"><rect width="15" height="12" rx="1" fill="#bbb"/><path d="M1 1l6.5 5L14 1" fill="none" stroke="#fff" stroke-width="1.5"/></svg>Phone</div>
  <div class="field" style="left:244px;top:4054px;width:739px;height:94px;align-items:flex-start;padding-top:18px">
    <svg width="15" height="13" viewBox="0 0 15 13"><ellipse cx="7.5" cy="5.5" rx="7.5" ry="5.5" fill="#bbb"/><path d="M3 9l-1 4 4-2z" fill="#bbb"/></svg>Leave Message</div>
  <div class="btn" style="left:518px;top:4174px;width:177px;height:48px;background:var(--slate);font-size:14px">BOOK NOW ›</div>

  <!-- FOOTER -->
  <div class="abs" style="left:510px;top:4282px;width:180px;height:140px;border-radius:90px 90px 0 0;background:var(--white);display:flex;align-items:center;justify-content:center">
    <span class="wordmark" style="font-size:26px">TALLWICK</span>
  </div>
  <span class="fnav" style="left:143px">HOME</span><span class="bullet" style="left:211px"></span>
  <span class="fnav" style="left:237px">ABOUT US</span><span class="bullet" style="left:340px"></span>
  <span class="fnav" style="left:366px">SERVICES</span>
  <span class="fnav" style="left:777px">WHY US</span><span class="bullet" style="left:864px"></span>
  <span class="fnav" style="left:889px">CONTACT</span><span class="bullet" style="left:993px"></span>
  <span class="fnav" style="left:1019px">BOOK NOW</span>
  <div class="abs" style="left:135px;top:4449px;width:980px;height:1px;background:var(--line)"></div>

  <div class="abs" style="left:157px;top:4472px;display:flex;align-items:center;gap:14px">
    <span class="dot-icon" style="width:44px;height:44px"><svg width="20" height="20" viewBox="0 0 24 24"><path d="M6.6 10.8a15 15 0 0 0 6.6 6.6l2.2-2.2c.3-.3.7-.4 1-.2 1.1.4 2.3.6 3.6.6.6 0 1 .4 1 1V20c0 .6-.4 1-1 1A17 17 0 0 1 3 4c0-.6.4-1 1-1h3.5c.6 0 1 .4 1 1 0 1.3.2 2.5.6 3.6.1.3 0 .7-.2 1z" fill="#fff"/></svg></span>
    <div style="font-size:13px;line-height:19px"><span style="color:#888">Phone Number</span><br>(+123) 555 0142</div>
  </div>
  <div class="abs" style="left:528px;top:4472px;display:flex;align-items:center;gap:14px">
    <span class="dot-icon" style="width:44px;height:44px"><svg width="20" height="15" viewBox="0 0 20 15"><rect width="20" height="15" rx="2" fill="#fff"/><path d="M1 1l9 7 9-7" fill="none" stroke="#e2a826" stroke-width="1.6"/></svg></span>
    <div style="font-size:13px;line-height:19px"><span style="color:#888">Email adress</span><br>info@tallwickhomeservices.com</div>
  </div>
  <svg class="abs" style="left:930px;top:4476px" width="170" height="38" viewBox="0 0 170 38">
    <circle cx="19" cy="19" r="18" fill="#e2a826"/><circle cx="62" cy="19" r="18" fill="#6d6d72"/>
    <circle cx="105" cy="19" r="18" fill="#6d6d72"/><circle cx="148" cy="19" r="18" fill="#6d6d72"/>
  </svg>
  <div class="abs" style="left:135px;top:4540px;width:980px;height:1px;background:var(--line)"></div>
  <p class="abs" style="left:0;width:1200px;top:4568px;text-align:center;font-size:13px;color:var(--slate)">Copyright © 2025 Tallwick Home Services . All Right Reserved</p>
  <div class="abs" style="left:1008px;top:4558px;width:107px;height:32px;border-radius:16px;background:#e3e3e3;display:flex;align-items:center;justify-content:flex-end;gap:8px;font-family:'Montserrat',sans-serif;font-size:9px;font-weight:700;color:var(--slate)">
    GO TO TOP
    <span style="width:32px;height:32px;border-radius:50%;background:var(--slate);display:flex;align-items:center;justify-content:center"><svg width="12" height="14" viewBox="0 0 12 14"><path d="M6 13V2M1 6l5-5 5 5" fill="none" stroke="#fff" stroke-width="2"/></svg></span>
  </div>

</div>
</body>
</html>
```